Smack you in the face - Landing page for Residential Electrical Repairs (Searchly Ads)

I need an effective landing page for Searchly ads. The ads will target residential electrical repairs. Lighting Outages, Power Outages, Breakers Tripping, Outlets Not Working. I need a strong call to action to Call Us Now! Forms don't work well for us so we only need one form as a last option at the bottom of the page. We only work on homes. the website is https://www.vantor-wiring.example/
email is : support@vantor-wiring.example
Phone 555-217-4086

**This is about one focused service. Electrical Repairs - That includes Partial Power Outages, Outlets Not Working, Tripped Breakers, Electrical Panel repairs, and Fusebox Repairs. The area served will only be Harlow Springs. KOBA is the platform

Target Market(s)

Homeonwers in need of electrical repair

Industry/Entity Type

Residential Electricians

Coding

Coded - Design and coding required

Requirements
Must have
• Strong to action for phone calls, this landing page must grab action fast.
Nice to have
• Social proof with existing 5 start reviews for Searchly, Rately, TCB, and Friendnet
Should not have
• Should not be form based. I do not like the site's current them, please don't copy it. Make your own.

```html
<!DOCTYPE html>
<html lang="en">
<head>
<meta charset="utf-8">
<title>Vantor Wiring Service – Residential Electrical Repair</title>
<link rel="stylesheet" href="https://fonts.googleapis.com/css2?family=Lexend:wght@500;600;700&family=Montserrat:wght@400;500;600;700&family=Barlow:wght@400;600&display=swap">
<style>
:root{
  --blue:#1f93c6;
  --blue-deep:#137bb0;
  --orange:#f06a22;
  --navy:#16303f;
  --ink:#1b1b1b;
  --text:#3a3a3a;
  --gray-bg:#eef0f2;
  --white:#ffffff;
  --black:#0b0b0b;
}
*{box-sizing:border-box;margin:0;padding:0}
html,body{width:1200px;height:4825px;overflow:hidden}
body{position:relative;font-family:"Montserrat",sans-serif;color:var(--text);background:var(--white)}
.abs{position:absolute}
.heading{font-family:"Lexend",sans-serif;font-weight:600;letter-spacing:2px;color:var(--ink);text-transform:uppercase}
.heading .accent{color:var(--blue)}
.rule{width:64px;height:3px;background:var(--orange)}
.btn{display:flex;align-items:center;gap:8px;background:var(--orange);color:var(--white);font-weight:700;font-size:17px;text-transform:uppercase;padding:0 22px;height:46px;text-decoration:none}
.btn svg{width:16px;height:16px;fill:var(--white)}
.photo{background:linear-gradient(135deg,#6f7c86,#b9c2c8 45%,#4d6477)}
.logo{color:var(--white);font-family:"Lexend",sans-serif;font-weight:700;text-align:center;line-height:1.1;letter-spacing:3px}

/* hero */
.hero{left:0;top:0;width:1200px;height:760px;background:linear-gradient(160deg,#1a8cc4,#2aa5d8 60%,#1f93c6);overflow:hidden}
.hero-photo{left:560px;top:0;width:640px;height:720px;background:linear-gradient(120deg,#3f6e8c,#a8b3ba 40%,#d9d3c8 75%,#8d8a83)}
.nav{left:0;top:0;width:1200px;height:88px}
.nav .logo{left:96px;top:22px;font-size:22px}
.nav .logo small{display:block;font-size:10px;letter-spacing:2.5px}
.nav ul{left:352px;top:36px;display:flex;gap:64px;list-style:none}
.nav a{color:var(--white);font-size:13px;font-weight:500;text-decoration:none}
.nav .active{border-bottom:2px solid var(--orange);padding-bottom:6px}
.nav-phone{left:950px;top:0;width:250px;height:88px;background:var(--orange);color:var(--white);display:flex;align-items:center;justify-content:center;gap:8px;font-weight:700;font-size:18px}
.nav-phone svg{width:22px;height:22px;fill:none;stroke:var(--white);stroke-width:2}
.hero-tag{left:114px;top:206px;background:var(--white);color:var(--blue);font-weight:600;font-size:17px;letter-spacing:1.5px;padding:5px 12px}
.hero-title{left:116px;top:250px;font-family:"Lexend",sans-serif;font-weight:600;color:var(--white);font-size:46px;line-height:52px;letter-spacing:4px}
.wave{left:0;top:560px;width:1200px;height:200px}

/* about */
.about-ring{left:92px;top:740px;width:486px;height:486px;border-radius:50%;border:1.5px solid #b6dcec}
.about-photo{left:130px;top:785px;width:400px;height:400px;border-radius:50%}
.about-title{left:630px;top:838px;font-size:33px;line-height:40px}
.about-text{left:630px;top:950px;width:490px;font-size:16px;line-height:27px}

/* repairs */
.repairs{left:0;top:1258px;width:1200px;height:792px;background:var(--gray-bg)}
.card{width:302px;height:224px}
.card .photo{position:absolute;left:0;top:0;width:302px;height:224px}
.card-label{position:absolute;left:20px;top:176px;width:264px;height:80px;background:var(--white);display:flex;align-items:center;gap:14px;padding:0 18px;font-size:14px;font-weight:600;text-transform:uppercase;color:var(--ink);line-height:18px;box-shadow:0 6px 14px rgba(0,0,0,.08)}
.card-label.on{background:var(--blue);color:var(--white)}
.card-label svg{width:34px;height:34px;fill:none;stroke:currentColor;stroke-width:1.6;flex:none}

/* cta band */
.cta-band{left:0;top:2050px;width:1200px;height:107px;background:var(--blue)}
.cta-band-orange{left:0;top:2050px;width:1200px;height:107px}
.cta-band-left{left:134px;top:2083px;font-family:"Lexend",sans-serif;font-weight:600;color:var(--white);font-size:25px;letter-spacing:1px}
.cta-band-right{left:750px;top:2080px;display:flex;align-items:center;gap:14px;font-family:"Lexend",sans-serif;font-weight:600;color:var(--white);font-size:26px;text-decoration:none}
.cta-band-right span.dot{width:38px;height:38px;border-radius:50%;background:var(--white);display:flex;align-items:center;justify-content:center}
.cta-band-right svg{width:20px;height:20px;fill:var(--orange)}

/* why */
.why-eyebrow{left:134px;top:2232px;font-size:14px;letter-spacing:2px;text-transform:uppercase}
.why-title{left:134px;top:2260px;font-size:29px;line-height:38px}
.why-photo{left:118px;top:2360px;width:430px;height:360px;background:radial-gradient(ellipse at 45% 55%,#4a5863,#a7b4bd 60%,rgba(255,255,255,0) 85%)}
.feature{width:254px;height:192px;padding:28px 34px;color:var(--white)}
.feature svg{width:38px;height:38px;fill:none;stroke:var(--white);stroke-width:1.6}
.feature h3{font-size:15px;font-weight:700;margin-top:14px;line-height:17px}
.feature p{font-size:11px;line-height:17px;margin-top:8px;opacity:.9}

/* reviews */
.reviews{left:0;top:2720px;width:1200px;height:590px;background:var(--gray-bg)}
.reviews-eyebrow{left:0;top:2776px;width:1200px;text-align:center;color:var(--blue);font-size:15px;letter-spacing:2px}
.review{width:306px;height:276px;background:var(--white);padding:26px 48px 0 48px;box-shadow:0 6px 18px rgba(0,0,0,.06)}
.review .q{font-size:40px;color:#9aa0a4;line-height:30px;height:30px}
.review p{font-size:12px;line-height:19px;margin-top:10px}
.review .by{font-size:13px;font-weight:600;color:var(--ink);margin-top:12px}
.review .city{font-size:10px;color:#8a8a8a;margin-top:3px}
.review .stars{color:var(--orange);font-size:17px;letter-spacing:1px;margin-top:2px}
.review .src{position:absolute;right:22px;bottom:30px;font-size:12px;font-weight:700;color:var(--blue)}
.arrow{width:24px;height:36px;fill:none;stroke:var(--blue);stroke-width:3}

/* emergency */
.emergency{left:0;top:3310px;width:1200px;height:560px;background:var(--blue)}
.em-photo{left:0;top:3310px;width:640px;height:560px}
.em-title{left:677px;top:3430px;color:var(--white);font-size:28px;line-height:38px}
.em-text{left:677px;top:3528px;width:425px;color:var(--white);font-size:15px;line-height:27px}

/* contact */
.contact-eyebrow{left:130px;top:3987px;color:var(--blue);font-size:16px;letter-spacing:2px}
.contact-title{left:130px;top:4020px;font-size:33px}
.info{left:130px;display:flex;align-items:center;gap:20px;font-family:"Barlow",sans-serif}
.info .ic{width:56px;height:56px;border-radius:50%;background:var(--blue);display:flex;align-items:center;justify-content:center}
.info .ic svg{width:26px;height:26px;fill:var(--white)}
.info small{display:block;font-size:18px;color:#444;text-transform:uppercase}
.info b{display:block;font-size:23px;font-weight:600;color:var(--ink)}
.info b.mail{font-weight:400;font-size:20px}
.form{left:598px;top:3965px;width:492px;height:410px;background:var(--orange);border-radius:70px 0 70px 0;padding:44px 45px 0 45px}
.field{height:44px;border:1.5px solid rgba(255,255,255,.85);display:flex;align-items:center;gap:10px;padding:0 18px;color:var(--white);font-size:13px;margin-bottom:10px}
.field svg{width:14px;height:14px;fill:var(--white)}
.field.area{height:82px;align-items:flex-start;padding-top:14px}
.submit{width:142px;height:38px;border-radius:20px;background:var(--blue);color:var(--white);font-size:13px;font-weight:700;display:flex;align-items:center;justify-content:center;margin-top:24px}

/* footer */
.footer{left:0;top:4455px;width:1200px;height:370px;background:var(--black)}
.fcol{top:4528px;color:var(--white)}
.fcol h4{font-family:"Lexend",sans-serif;font-weight:600;font-size:16px;letter-spacing:1px}
.fcol .bar{width:44px;height:2px;background:var(--blue);margin:6px 0 16px}
.fcol p{font-size:12px;line-height:23px;display:flex;align-items:center;gap:8px}
.fcol p svg{width:16px;height:16px;fill:var(--white)}
.copy{left:0;top:4780px;width:1200px;text-align:center;font-size:11px;color:var(--white);border-top:1px solid #2a2a2a;padding-top:14px}
</style>
</head>
<body>

<!-- HERO -->
<section class="abs hero">
  <div class="abs hero-photo" role="img" aria-label="Electrician in a dark work shirt wiring a residential breaker panel"></div>
  <svg class="abs wave" viewBox="0 0 1200 200" preserveAspectRatio="none">
    <path d="M0 185 C 300 95, 700 70, 1200 140 L1200 200 L0 200Z" fill="#ffffff"/>
    <path d="M0 175 C 300 85, 700 60, 1200 128" fill="none" stroke="#1f93c6" stroke-width="4"/>
  </svg>
</section>

<nav class="abs nav">
  <div class="abs logo">VANTOR<small>WIRING SERVICE</small></div>
  <ul class="abs">
    <li><a class="active" href="#">HOME</a></li>
    <li><a href="#">ABOUT US</a></li>
    <li><a href="#">SERVICES</a></li>
    <li><a href="#">REVIEWS</a></li>
    <li><a href="#">CONTACT</a></li>
  </ul>
  <a class="abs nav-phone" href="tel:5552174086"><svg viewBox="0 0 24 24"><circle cx="12" cy="12" r="10"/><path d="M9 7l2 3-1.5 1.5a7 7 0 0 0 3 3L14 13l3 2-1 2c-4 0-8-4-8-8z" fill="#fff" stroke="none"/></svg>555-217-4086</a>
</nav>

<div class="abs hero-tag">VANTOR WIRING SERVICES</div>
<h1 class="abs hero-title">RESIDENTIAL<br>FOR ELECTRICAL<br>REPAIR SOLUTION</h1>
<a class="abs btn" href="tel:5552174086" style="left:112px;top:420px"><svg viewBox="0 0 24 24"><path d="M6.6 10.8a15 15 0 0 0 6.6 6.6l2.2-2.2a1 1 0 0 1 1-.25 11 11 0 0 0 3.6.6 1 1 0 0 1 1 1V20a1 1 0 0 1-1 1A17 17 0 0 1 3 4a1 1 0 0 1 1-1h3.5a1 1 0 0 1 1 1c0 1.25.2 2.45.6 3.6a1 1 0 0 1-.25 1z"/></svg>Call us now</a>

<!-- ABOUT -->
<div class="abs about-ring"></div>
<div class="abs about-photo photo" role="img" aria-label="Technician in a blue cap working on a home breaker panel"></div>
<h2 class="abs heading about-title">About Vantor<br><span class="accent">Electrical Repair</span></h2>
<p class="abs about-text">At Vantor Wiring, EV Chargers, &amp; Generators, your electrical emergency is our urgency. We have Licensed Electricians in Harlow Springs, Oakmere, and Castleton, ensuring top-tier service for every call. We've built our reputation as the go-to Emergency Electrician for homeowners in need.</p>

<!-- REPAIRS -->
<section class="abs repairs"></section>
<h2 class="abs heading" style="left:0;top:1314px;width:1200px;text-align:center;font-size:30px">Electrical <span class="accent">Repair</span></h2>
<div class="abs rule" style="left:568px;top:1362px"></div>

<div class="abs card" style="left:115px;top:1405px">
  <div class="photo" role="img" aria-label="Multimeter probes testing an outlet box"></div>
  <div class="card-label"><svg viewBox="0 0 32 32"><path d="M16 3 30 28H2Z"/><path d="M17 10l-4 8h4l-2 6"/></svg>Partial power<br>outages</div>
</div>
<div class="abs card" style="left:440px;top:1405px">
  <div class="photo" role="img" aria-label="Hand holding a wall outlet with wires"></div>
  <div class="card-label on"><svg viewBox="0 0 32 32"><rect x="3" y="9" width="26" height="14" rx="2"/><circle cx="11" cy="16" r="3"/><circle cx="21" cy="16" r="3"/></svg>Outlets not<br>working</div>
</div>
<div class="abs card" style="left:767px;top:1405px">
  <div class="photo" role="img" aria-label="Hand resetting a circuit breaker"></div>
  <div class="card-label"><svg viewBox="0 0 32 32"><rect x="5" y="4" width="22" height="24" rx="2"/><path d="M9 10h14M9 16h14M9 22h14"/></svg>Tripped<br>breakers</div>
</div>
<div class="abs card" style="left:278px;top:1718px">
  <div class="photo" role="img" aria-label="Electrician in a hard hat at an outdoor panel"></div>
  <div class="card-label"><svg viewBox="0 0 32 32"><rect x="4" y="4" width="24" height="24"/><path d="M9 9h6v6H9zM17 9h6v6h-6zM9 17h14v6H9z"/></svg>Electrical panel<br>repairs</div>
</div>
<div class="abs card" style="left:630px;top:1718px">
  <div class="photo" role="img" aria-label="Electrician working inside a fuse box"></div>
  <div class="card-label"><svg viewBox="0 0 32 32"><rect x="6" y="3" width="20" height="26" rx="2"/><rect x="11" y="9" width="10" height="14"/></svg>Fusebox<br>repairs</div>
</div>

<!-- CTA BAND -->
<section class="abs cta-band"></section>
<svg class="abs cta-band-orange" viewBox="0 0 1200 107" preserveAspectRatio="none"><polygon points="735,0 1200,0 1200,107 700,107" fill="#f06a22"/></svg>
<div class="abs cta-band-left">24/7 ELECTRICAL REPAIR SERVICE NOW!</div>
<a class="abs cta-band-right" href="tel:5552174086"><span class="dot"><svg viewBox="0 0 24 24"><path d="M6.6 10.8a15 15 0 0 0 6.6 6.6l2.2-2.2a1 1 0 0 1 1-.25 11 11 0 0 0 3.6.6 1 1 0 0 1 1 1V20a1 1 0 0 1-1 1A17 17 0 0 1 3 4a1 1 0 0 1 1-1h3.5a1 1 0 0 1 1 1c0 1.25.2 2.45.6 3.6a1 1 0 0 1-.25 1z"/></svg></span>CALL US 555-217-4086</a>

<!-- WHY -->
<div class="abs why-eyebrow">Why we are</div>
<h2 class="abs heading why-title">Why choose Vantor<br><span class="accent">Electrical Service</span></h2>
<div class="abs rule" style="left:136px;top:2342px"></div>
<div class="abs why-photo" role="img" aria-label="Smiling electrician in a blue cap holding wiring tools"></div>

<div class="abs feature" style="left:568px;top:2220px;background:var(--blue)">
  <svg viewBox="0 0 32 32"><rect x="4" y="6" width="24" height="22" rx="2"/><path d="M4 12h24M10 3v6M22 3v6M9 17h3M15 17h3M21 17h3M9 22h3M15 22h3"/></svg>
  <h3>On-Time<br>Appointments</h3>
  <p>We arrive in the window we promise, every visit.</p>
</div>
<div class="abs feature" style="left:568px;top:2430px;background:var(--navy)">
  <svg viewBox="0 0 32 32"><circle cx="16" cy="16" r="13" stroke-dasharray="60 8"/><text x="16" y="20" font-size="10" text-anchor="middle" fill="#fff" stroke="none" font-family="Montserrat">24/7</text></svg>
  <h3>Same Day Service</h3>
  <p>Call before noon and most repairs are finished the same afternoon.</p>
</div>
<div class="abs feature" style="left:840px;top:2304px;background:var(--orange)">
  <svg viewBox="0 0 32 32"><circle cx="16" cy="16" r="12" stroke-dasharray="3 2"/><circle cx="16" cy="16" r="7"/><path d="M13 16l2 2 4-4"/></svg>
  <h3>100% Satisfaction<br>Gurantee</h3>
  <p>If it is not right, we come back free.</p>
</div>

<!-- REVIEWS -->
<section class="abs reviews"></section>
<div class="abs reviews-eyebrow">TESTIMONIALS</div>
<h2 class="abs heading" style="left:0;top:2804px;width:1200px;text-align:center;font-size:30px">Customer <span class="accent">Reviews</span></h2>
<div class="abs rule" style="left:568px;top:2848px"></div>

<svg class="abs arrow" style="left:72px;top:3000px" viewBox="0 0 24 36"><path d="M18 4 6 18l12 14"/></svg>
<svg class="abs arrow" style="left:1128px;top:3000px" viewBox="0 0 24 36"><path d="M6 4l12 14L6 32"/></svg>

<article class="abs review" style="left:134px;top:2888px">
  <div class="q">&ldquo;</div>
  <p>Our kitchen outlets died on a Sunday. They came out within two hours, found a failed breaker, and replaced it cleanly. Fair price and friendly tech.</p>
  <div class="by">By Author Name</div><div class="city">City Name</div>
  <div class="stars">★★★★★</div>
  <div class="src">Searchly</div>
</article>
<article class="abs review" style="left:460px;top:2888px">
  <div class="q">&ldquo;</div>
  <p>Half the house lost power after a storm. The electrician traced the fault to the panel and had everything working again before dinner. Highly recommend.</p>
  <div class="by">By Author Name</div><div class="city">City Name</div>
  <div class="stars">★★★★★</div>
  <div class="src">Searchly</div>
</article>
<article class="abs review" style="left:786px;top:2888px">
  <div class="q">&ldquo;</div>
  <p>Our old fuse box kept blowing. They explained every option clearly, upgraded it the next day, and left the basement cleaner than they found it.</p>
  <div class="by">By Author Name</div><div class="city">City Name</div>
  <div class="stars">★★★★★</div>
  <div class="src">Friendnet</div>
</article>

<a class="abs btn" href="tel:5552174086" style="left:512px;top:3207px"><svg viewBox="0 0 24 24"><path d="M6.6 10.8a15 15 0 0 0 6.6 6.6l2.2-2.2a1 1 0 0 1 1-.25 11 11 0 0 0 3.6.6 1 1 0 0 1 1 1V20a1 1 0 0 1-1 1A17 17 0 0 1 3 4a1 1 0 0 1 1-1h3.5a1 1 0 0 1 1 1c0 1.25.2 2.45.6 3.6a1 1 0 0 1-.25 1z"/></svg>Call us now</a>

<!-- EMERGENCY -->
<section class="abs emergency"></section>
<svg class="abs em-photo" viewBox="0 0 640 560" role="img" aria-label="Electrician in a light blue shirt repairing an outdoor electrical panel">
  <defs><linearGradient id="emg" x1="0" y1="0" x2="1" y2="1"><stop offset="0" stop-color="#c9cfd3"/><stop offset=".5" stop-color="#7e96ab"/><stop offset="1" stop-color="#4b5b66"/></linearGradient></defs>
  <path d="M0 0H470C610 120 640 380 560 560H0Z" fill="#ffffff"/>
  <path d="M0 0H460C595 120 625 380 545 560H0Z" fill="url(#emg)"/>
</svg>
<h2 class="abs heading em-title" style="color:#fff">Emergency<br>Electrical Services</h2>
<p class="abs em-text">Vantor Wiring, your trusted partner in handling electrical emergencies. We understand that electrical issues demand immediate attention to ensure the safety of your home and loved ones. With our commitment to excellence, we offer unparalleled services in Northside Harlow Springs, Eastside Oakmere, and the Castleton area.</p>
<a class="abs btn" href="tel:5552174086" style="left:677px;top:3745px"><svg viewBox="0 0 24 24"><path d="M6.6 10.8a15 15 0 0 0 6.6 6.6l2.2-2.2a1 1 0 0 1 1-.25 11 11 0 0 0 3.6.6 1 1 0 0 1 1 1V20a1 1 0 0 1-1 1A17 17 0 0 1 3 4a1 1 0 0 1 1-1h3.5a1 1 0 0 1 1 1c0 1.25.2 2.45.6 3.6a1 1 0 0 1-.25 1z"/></svg>Call us now</a>

<!-- CONTACT -->
<div class="abs contact-eyebrow">GET IN TOUCH</div>
<h2 class="abs heading contact-title">Contact <span class="accent">Us</span></h2>

<div class="abs info" style="top:4100px">
  <span class="ic"><svg viewBox="0 0 24 24"><path d="M12 2a7 7 0 0 0-7 7c0 5 7 13 7 13s7-8 7-13a7 7 0 0 0-7-7zm0 9.5A2.5 2.5 0 1 1 12 6.5a2.5 2.5 0 0 1 0 5z"/></svg></span>
  <div><small>Area serve</small><b>Harlow Springs</b></div>
</div>
<div class="abs info" style="top:4190px">
  <span class="ic"><svg viewBox="0 0 24 24"><path d="M6.6 10.8a15 15 0 0 0 6.6 6.6l2.2-2.2a1 1 0 0 1 1-.25 11 11 0 0 0 3.6.6 1 1 0 0 1 1 1V20a1 1 0 0 1-1 1A17 17 0 0 1 3 4a1 1 0 0 1 1-1h3.5a1 1 0 0 1 1 1c0 1.25.2 2.45.6 3.6a1 1 0 0 1-.25 1z"/></svg></span>
  <div><small>Phone number</small><b>555-217-4086</b></div>
</div>
<div class="abs info" style="top:4280px">
  <span class="ic"><svg viewBox="0 0 24 24"><path d="M3 6h18v12H3z" fill="none" stroke="#fff" stroke-width="2"/><path d="M3 6l9 7 9-7" fill="none" stroke="#fff" stroke-width="2"/></svg></span>
  <div><small>Email us</small><b class="mail">support@vantor-wiring.example</b></div>
</div>

<form class="abs form" action="#">
  <div class="field"><svg viewBox="0 0 24 24"><circle cx="12" cy="7" r="5"/><path d="M2 23c0-6 4-9 10-9s10 3 10 9z"/></svg>First name</div>
  <div class="field"><svg viewBox="0 0 24 24"><circle cx="12" cy="7" r="5"/><path d="M2 23c0-6 4-9 10-9s10 3 10 9z"/></svg>Last name</div>
  <div class="field"><svg viewBox="0 0 24 24"><path d="M6.6 10.8a15 15 0 0 0 6.6 6.6l2.2-2.2a1 1 0 0 1 1-.25 11 11 0 0 0 3.6.6 1 1 0 0 1 1 1V20a1 1 0 0 1-1 1A17 17 0 0 1 3 4a1 1 0 0 1 1-1h3.5a1 1 0 0 1 1 1c0 1.25.2 2.45.6 3.6a1 1 0 0 1-.25 1z"/></svg>Phone number</div>
  <div class="field"><svg viewBox="0 0 24 24"><path d="M2 5h20v14H2zM2 5l10 8 10-8" stroke="#f06a22" stroke-width="1.5"/></svg>Email address</div>
  <div class="field area">Comments</div>
  <div class="submit">SUBMIT ›</div>
</form>

<!-- FOOTER -->
<footer class="abs footer"></footer>
<div class="abs logo" style="left:140px;top:4560px;font-size:30px">VANTOR<small style="display:block;font-size:13px;letter-spacing:3px">WIRING SERVICE</small></div>

<div class="abs fcol" style="left:441px">
  <h4>QUICK LINKS</h4><div class="bar"></div>
  <p>About Us</p><p>Our Equipments</p><p>Ambulance</p><p>Partners</p><p>Blogs</p>
</div>
<div class="abs fcol" style="left:653px">
  <h4>CONTACT US</h4><div class="bar"></div>
  <p><svg viewBox="0 0 24 24"><path d="M6.6 10.8a15 15 0 0 0 6.6 6.6l2.2-2.2a1 1 0 0 1 1-.25 11 11 0 0 0 3.6.6 1 1 0 0 1 1 1V20a1 1 0 0 1-1 1A17 17 0 0 1 3 4a1 1 0 0 1 1-1h3.5a1 1 0 0 1 1 1c0 1.25.2 2.45.6 3.6a1 1 0 0 1-.25 1z"/></svg>(555) 217-4086</p>
  <p style="margin-top:8px"><svg viewBox="0 0 24 24"><path d="M2 5h20v14H2z"/></svg>support@vantor-wiring.example</p>
</div>
<div class="abs fcol" style="left:898px">
  <h4>FOLLOW US</h4><div class="bar"></div>
  <p>Friendnet</p><p>Chirpr</p><p>Pictly</p>
</div>
<div class="abs copy">Copyright © 2023 - Lumen Studio - All rights reserved</div>

</body>
</html>
```